Boston area Multi-store hair salon needs a poster for a special service

We need a poster for a soon to be multi-store hair salon based in the Boston area. We are expanding, opening more salons. We need a poster for a service we offer called "The Fullset!" It is for men, and it includes:
1. Haircut
2. Shampoo
3. Neck Shave
4. Hot Towel Service

We charge $22 for The Fullset!
70% of our clients are men.
Our website is www.trimvane.example
Our colors are black and red
***Please focus on the "The Fullset!" part of the poster. We are almost looking for logo or icon for The Fullset! part. *****
This will be hung inside the store near the reception area and possibly through out the salon and could be included in emails.
I have attached our logo and some other branding items we use (business cards, rewards cards, envelopes, etc) to help give you an idea of the look and feel we currently have. I have also attached an ad from Pelham which is a coupon they use for a service they call the fullset, just to give an idea. We like how Pelham created "The Fullset" as an icon or logo.

Target Market(s)

Men

Industry/Entity Type

Store

Requirements
Nice to have
• Pictures of each service. We uploaded some examples.
• Also, "The Fullset!" should be like a logo/icon

```html
<!DOCTYPE html>
<html lang="en">
<head>
<meta charset="utf-8">
<title>The Fullset! – Trimvane</title>
<link rel="stylesheet" href="https://fonts.googleapis.com/css2?family=Montserrat:wght@700;800;900&family=Nunito:wght@900&display=swap">
<style>
  :root {
    --ink: #151515;
    --charcoal: #2b2b2b;
    --graphite: #3a3a3a;
    --red: #d4121c;
    --red-deep: #9e0b12;
    --white: #ffffff;
    --silver-light: #f2f2f2;
    --silver-mid: #b9b9b9;
    --silver-dark: #6f6f6f;
  }
  * { margin: 0; padding: 0; box-sizing: border-box; }
  html, body { width: 800px; height: 1200px; overflow: hidden; background: var(--ink); }
  .poster {
    position: relative;
    width: 800px;
    height: 1200px;
    overflow: hidden;
    background: radial-gradient(ellipse at 65% 20%, var(--graphite) 0%, var(--charcoal) 35%, var(--ink) 80%);
    font-family: "Montserrat", Arial, sans-serif;
    color: var(--white);
  }
  .poster__band, .poster__headline, .price-tag__string { position: absolute; left: 0; top: 0; }
  .brand-mark {
    position: absolute;
    left: 524px; top: 90px;
    width: 170px; height: 170px;
    border-radius: 50%;
    background: var(--ink);
    border: 4px solid var(--silver-mid);
    display: flex; align-items: center; justify-content: center;
    font-family: "Montserrat", Arial, sans-serif;
    font-weight: 900;
    font-size: 26px;
    letter-spacing: 1px;
    color: var(--white);
  }
  .services {
    position: absolute;
    left: 180px; top: 600px;
    list-style: none;
  }
  .services__item {
    display: flex; align-items: center;
    height: 66px;
    font-weight: 800;
    font-size: 33px;
    letter-spacing: 1px;
  }
  .services__arrow {
    width: 24px; height: 20px; margin-right: 24px; flex: none;
  }
  .price-tag {
    position: absolute;
    left: 558px; top: 566px;
    width: 212px; height: 212px;
    border-radius: 50%;
    background: radial-gradient(circle at 50% 35%, #2e2e2e, #0d0d0d 75%);
    border: 4px solid var(--silver-mid);
    box-shadow: 0 0 0 2px #555, 0 6px 14px rgba(0,0,0,.6);
    text-align: center;
    display: flex; flex-direction: column; justify-content: center; align-items: center;
  }
  .price-tag__lead, .price-tag__tail { font-weight: 800; font-size: 14px; letter-spacing: .5px; }
  .price-tag__amount {
    font-family: "Nunito", Arial, sans-serif;
    font-weight: 900; font-size: 82px; line-height: 1;
    color: var(--red);
    -webkit-text-stroke: 2px var(--white);
    margin: 2px 0;
  }
  .website {
    position: absolute;
    left: 258px; top: 1104px;
    font-weight: 800;
    font-size: 38px;
    letter-spacing: .5px;
  }
</style>
</head>
<body>
<main class="poster">
  <svg class="poster__band" width="800" height="1200" viewBox="0 0 800 1200" aria-hidden="true">
    <defs>
      <linearGradient id="bandRed" x1="0" y1="0" x2="1" y2="0">
        <stop offset="0" stop-color="var(--red-deep)"/>
        <stop offset="1" stop-color="var(--red)"/>
      </linearGradient>
    </defs>
    <path d="M0,0 H360 C200,40 80,200 62,420 C45,660 130,920 240,1200 H0 Z" fill="url(#bandRed)"/>
    <path d="M330,-4 C170,50 58,210 42,420 C26,660 105,920 208,1204" fill="none" stroke="var(--white)" stroke-width="16"/>
  </svg>

  <div class="brand-mark">TRIMVANE</div>

  <svg class="poster__headline" width="800" height="560" viewBox="0 0 800 560">
    <defs>
      <linearGradient id="chrome" x1="0" y1="0" x2="0" y2="1">
        <stop offset="0" stop-color="var(--silver-light)"/>
        <stop offset=".5" stop-color="var(--silver-mid)"/>
        <stop offset=".55" stop-color="var(--silver-dark)"/>
        <stop offset="1" stop-color="var(--silver-light)"/>
      </linearGradient>
    </defs>
    <text x="80" y="390" textLength="204" lengthAdjust="spacingAndGlyphs"
          font-family="Nunito, Arial, sans-serif" font-weight="900" font-size="110"
          fill="url(#chrome)" stroke="#555" stroke-width="1.5">The</text>
    <text x="100" y="510" textLength="644" lengthAdjust="spacingAndGlyphs"
          font-family="Nunito, Arial, sans-serif" font-weight="900" font-size="140"
          fill="url(#chrome)" stroke="#555" stroke-width="1.5">FULLSET!</text>
    <path class="headline__tick" d="M298,362 L316,350 L332,376 C348,340 362,320 378,306 L372,330 C358,352 346,374 338,394 L324,394 Z"
          fill="var(--red)" stroke="var(--red-deep)" stroke-width="3" stroke-linejoin="round"/>
  </svg>

  <svg class="price-tag__string" width="800" height="620" viewBox="0 0 800 620" aria-hidden="true">
    <path d="M604,482 C592,508 600,530 642,548" fill="none" stroke="var(--silver-light)" stroke-width="2"/>
    <circle cx="654" cy="558" r="12" fill="none" stroke="var(--silver-light)" stroke-width="3"/>
  </svg>

  <ul class="services">
    <li class="services__item"><svg class="services__arrow" viewBox="0 0 24 20" aria-hidden="true"><path d="M0,0 L24,10 L0,20 L6,10 Z" fill="var(--red)"/></svg>HAIRCUT</li>
    <li class="services__item"><svg class="services__arrow" viewBox="0 0 24 20" aria-hidden="true"><path d="M0,0 L24,10 L0,20 L6,10 Z" fill="var(--red)"/></svg>SHAMPOO</li>
    <li class="services__item"><svg class="services__arrow" viewBox="0 0 24 20" aria-hidden="true"><path d="M0,0 L24,10 L0,20 L6,10 Z" fill="var(--red)"/></svg>NECK SHAVE</li>
    <li class="services__item"><svg class="services__arrow" viewBox="0 0 24 20" aria-hidden="true"><path d="M0,0 L24,10 L0,20 L6,10 Z" fill="var(--red)"/></svg>HOT TOWEL SERVICE</li>
  </ul>

  <div class="price-tag">
    <span class="price-tag__lead">WE CHARGE</span>
    <span class="price-tag__amount">$22</span>
    <span class="price-tag__tail">FOR THE FULLSET!</span>
  </div>

  <p class="website">www.trimvane.example</p>
</main>
</body>
</html>
```